Business Card Design

WE are looking for a premium quality Business Cards for a Law Firm . Copies of our current business card is attached.

Contact Information for Business Card

xyz

```html
<!DOCTYPE html>
<html lang="en">
<head>
<meta charset="utf-8">
<title>Ashcombe Lawyers – Business Card</title>
<link rel="stylesheet" href="https://fonts.googleapis.com/css2?family=Tinos:wght@400;700&display=swap">
<style>
  :root {
    --bg: #ece8e1;
    --green: #0c2b20;
    --green-soft: #143a2c;
    --gold: #c7a862;
    --gold-pale: #f1ebdc;
    --ink: #111111;
    --white: #ffffff;
  }
  * { box-sizing: border-box; margin: 0; padding: 0; }
  html, body {
    width: 1200px; height: 780px; overflow: hidden;
    background: var(--bg);
    font-family: "Tinos", "Times New Roman", serif;
  }
  .canvas {
    position: relative; width: 1200px; height: 780px;
    display: flex; align-items: center; justify-content: center; gap: 40px;
  }
  .card {
    position: relative; width: 540px; height: 330px;
    border-radius: 18px; overflow: hidden;
    box-shadow: 0 10px 30px rgba(0,0,0,.18);
  }

  /* ---------- Front ---------- */
  .card-front { background: var(--white); color: var(--ink); }
  .front-ring {
    position: absolute; left: 230px; top: 70px;
    width: 330px; height: 330px; border-radius: 50%;
    border: 14px solid var(--gold-pale);
  }
  .brand {
    position: absolute; display: flex; align-items: center; gap: 10px;
    font-weight: 700; letter-spacing: .08em; text-transform: uppercase;
    white-space: nowrap;
  }
  .brand-dot {
    width: 30px; height: 30px; border-radius: 50%;
    border: 3px solid var(--gold); flex: none;
  }
  .card-front .brand { left: 36px; top: 30px; color: var(--green); font-size: 20px; }
  .front-address {
    position: absolute; left: 36px; top: 82px;
    font-size: 14px; font-weight: 700; font-style: normal; line-height: 1.35;
  }
  .contact-list {
    position: absolute; left: 36px; top: 150px; list-style: none;
    font-size: 13.5px; font-weight: 700; line-height: 1.55;
  }
  .contact-list li { display: flex; align-items: center; gap: 8px; white-space: nowrap; }
  .contact-list svg { width: 13px; height: 13px; flex: none; }
  .front-person { position: absolute; left: 276px; top: 218px; white-space: nowrap; }
  .person-name {
    color: var(--gold); font-size: 26px; font-weight: 700;
    letter-spacing: .04em; text-transform: uppercase;
  }
  .person-role { font-size: 16px; font-weight: 700; margin-top: 4px; line-height: 1.3; }
  .front-tab {
    position: absolute; right: 0; top: 120px; width: 26px; height: 46px;
    background: var(--green);
  }

  /* ---------- Back ---------- */
  .card-back { background: var(--green); color: var(--white); }
  .back-pattern {
    position: absolute; inset: 0;
    background: radial-gradient(circle at 85% 30%, var(--green-soft), var(--green) 65%);
  }
  .card-back .brand {
    left: 0; right: 0; top: 36px; justify-content: center;
    color: var(--white); font-size: 26px;
  }
  .tagline-band {
    position: absolute; left: 0; right: 0; top: 108px; height: 28px;
    background: var(--gold); color: var(--green);
    display: flex; align-items: center; justify-content: center;
    font-size: 14px; font-weight: 700; letter-spacing: .06em; text-transform: uppercase;
  }
  .offices {
    position: absolute; left: 22px; right: 22px; top: 160px; bottom: 20px;
    display: grid; grid-template-columns: repeat(3, 1fr);
  }
  .office { padding: 6px 12px; font-size: 11.5px; line-height: 1.4; }
  .office + .office { border-left: 1px solid rgba(255,255,255,.7); }
  .office-city {
    color: var(--gold); font-size: 15px; font-weight: 700;
    letter-spacing: .05em; margin-bottom: 4px;
  }
  .office-phone { display: flex; align-items: center; gap: 6px; margin-top: 3px; }
  .office-phone svg { width: 11px; height: 11px; }
</style>
</head>
<body>
<main class="canvas">

  <section class="card card-front" aria-label="Business card front">
    <div class="front-ring"></div>
    <div class="brand"><span class="brand-dot"></span>Ashcombe Lawyers</div>
    <address class="front-address">
      Suite 410, Harlow Chambers,<br>
      212 Lantern Lane,<br>
      Melbourne VIC 3000
    </address>
    <ul class="contact-list">
      <li>
        <svg viewBox="0 0 16 16" fill="#c7a862"><path d="M3 1l3 3-2 2c1 2 3 4 5 5l2-2 3 3-2 3C7 15 1 9 1 3z"/></svg>
        +61 7 3900 1478
      </li>
      <li>
        <svg viewBox="0 0 16 16" fill="none" stroke="#c7a862" stroke-width="1.6"><rect x="4" y="1" width="8" height="14" rx="1.5"/></svg>
        +61 0400 362 917
      </li>
      <li>
        <svg viewBox="0 0 16 16" fill="none" stroke="#c7a862" stroke-width="1.5"><circle cx="8" cy="8" r="6.5"/><path d="M1.5 8h13M8 1.5c3 3 3 10 0 13M8 1.5c-3 3-3 10 0 13"/></svg>
        www.ashcombelawyers.com.au
      </li>
      <li>
        <svg viewBox="0 0 16 16" fill="none" stroke="#c7a862" stroke-width="1.5"><rect x="1.5" y="3.5" width="13" height="9" rx="1"/><path d="M1.5 4l6.5 5 6.5-5"/></svg>
        daniel@ashcombelawyers.com.au
      </li>
    </ul>
    <div class="front-person">
      <p class="person-name">Daniel Marlow</p>
      <p class="person-role">Director and Principal Solicitor<br>MBA, Juris Doctor</p>
    </div>
    <div class="front-tab"></div>
  </section>

  <section class="card card-back" aria-label="Business card back">
    <div class="back-pattern" role="img" aria-label="Repeating monogram pattern in dark green tones"></div>
    <div class="brand"><span class="brand-dot"></span>Ashcombe Lawyers</div>
    <div class="tagline-band">Clear counsel. Lasting results. Always</div>
    <div class="offices">
      <div class="office">
        <p class="office-city">MELBOURNE</p>
        <p>Level 19, 88 Quarry Street,<br>MELBOURNE, VIC 3000</p>
        <p class="office-phone"><svg viewBox="0 0 16 16" fill="#c7a862"><path d="M3 1l3 3-2 2c1 2 3 4 5 5l2-2 3 3-2 3C7 15 1 9 1 3z"/></svg>+61 03 9000 3186</p>
      </div>
      <div class="office">
        <p class="office-city">SYDNEY</p>
        <p>Level 12, Halden House<br>74 Ferry Street<br>PARRAMATTA, NSW 2150</p>
        <p class="office-phone"><svg viewBox="0 0 16 16" fill="#c7a862"><path d="M3 1l3 3-2 2c1 2 3 4 5 5l2-2 3 3-2 3C7 15 1 9 1 3z"/></svg>+61 02 9000 4721</p>
      </div>
      <div class="office">
        <p class="office-city">PERTH</p>
        <p>Level 31, Corvel Tower<br>156 Banksia Terrace<br>PERTH, WA 6000</p>
        <p class="office-phone"><svg viewBox="0 0 16 16" fill="#c7a862"><path d="M3 1l3 3-2 2c1 2 3 4 5 5l2-2 3 3-2 3C7 15 1 9 1 3z"/></svg>+61 08 9000 5863</p>
      </div>
    </div>
  </section>

</main>
</body>
</html>
```